Dovecote Realty

Business cards for 4 people

They need to say for all
87 Tarrow Quay, Boston MA 02114

Each person will have their own personal information
We would like gold embossing for the name of the company
Marla is the blonde sitting in the chair smiling her information should be on the back of the card with her name and information
Should say for slogan Timeless Homes, Refined Service
marla@dovecoteprops.com
(413) 555-0182

Odette is the brunette with wavy hair in the tan suit celina@dovecoteprops.com
(617) 555-0137

faith@dovecoteprops.com
(413) 555-0164
standing next to the chair

hope@dovecoteprops.com
(413) 555-0199
close up headshot

```html
<!DOCTYPE html>
<html lang="en">
<head>
<meta charset="utf-8">
<title>Dovecote Realty – Business Cards</title>
<link rel="stylesheet" href="https://fonts.googleapis.com/css2?family=Cinzel:wght@600&family=Lato:wght@400&display=swap">
<style>
  :root {
    --backdrop: #e9e6e1;
    --navy: #1d2f55;
    --navy-deep: #0d1a3a;
    --gold: #d6a84a;
    --gold-light: #f0cf7e;
    --gold-dark: #a9792a;
    --ink-light: #f3f1ec;
    --photo-light: #d9d9d9;
    --photo-mid: #bdbdbd;
  }
  * { margin: 0; padding: 0; box-sizing: border-box; }
  html, body {
    width: 1200px; height: 900px; overflow: hidden;
    background: var(--backdrop);
  }
  .stage { position: relative; width: 1200px; height: 900px; }

  .card {
    position: absolute;
    width: 640px; height: 366px;
    border-radius: 4px;
    overflow: hidden;
    box-shadow: 0 10px 28px rgba(0,0,0,.22);
  }

  /* Front card */
  .card--front { left: 90px; top: 60px; display: flex; background: var(--navy); }
  .portrait {
    width: 252px; height: 100%;
    background: linear-gradient(160deg, var(--photo-light), var(--photo-mid));
  }
  .divider {
    width: 8px; height: 100%;
    background: linear-gradient(180deg, var(--gold-dark), var(--gold-light) 45%, var(--gold-dark));
  }
  .details {
    flex: 1;
    padding: 40px 30px 0 40px;
    color: var(--ink-light);
    font-family: "Lato", sans-serif;
  }
  .brand__name {
    display: block;
    font-family: "Cinzel", serif; font-weight: 600;
    font-size: 24px; letter-spacing: .5px; line-height: 1.2;
    color: var(--gold);
    margin-bottom: 34px;
  }
  .person__name {
    font-family: "Cinzel", serif; font-weight: 600;
    font-size: 18px; letter-spacing: .8px;
    color: var(--gold);
  }
  .person__role { font-size: 15px; margin-top: 3px; margin-bottom: 22px; }
  .contact { list-style: none; font-size: 15px; }
  .contact li { display: flex; align-items: center; gap: 10px; height: 27px; }
  .contact svg { width: 16px; height: 16px; flex: none; }
  .rule { height: 1.5px; background: var(--gold); margin: 10px 0; width: 290px; }
  .slogan { font-size: 15px; letter-spacing: .3px; }

  /* Back card */
  .card--back {
    left: 470px; top: 474px;
    background: radial-gradient(ellipse at 50% 45%, #22345e 0%, var(--navy-deep) 75%);
    display: flex; align-items: center; justify-content: center;
  }
  .card--back .brand__name { font-size: 44px; letter-spacing: 2px; margin: 0; }
</style>
</head>
<body>
<main class="stage">

  <section class="card card--front">
    <div class="portrait" role="img" aria-label="Portrait photo of Marla seated on a wooden chair"></div>
    <div class="divider"></div>
    <div class="details">
      <span class="brand__name">DOVECOTE REALTY</span>
      <p class="person__name">MARLA ASHCOMBE</p>
      <p class="person__role">Real Estate Advisor and Rentals Manager</p>
      <ul class="contact">
        <li>
          <svg viewBox="0 0 16 16" aria-hidden="true"><rect x="4" y="1" width="8" height="14" rx="1.5" fill="none" stroke="var(--gold)" stroke-width="1.4"/><line x1="7" y1="12.5" x2="9" y2="12.5" stroke="var(--gold)" stroke-width="1.2"/></svg>
          (413) 555-0182
        </li>
        <li>
          <svg viewBox="0 0 16 16" aria-hidden="true"><rect x="1" y="3.5" width="14" height="9" fill="var(--gold)"/><polyline points="1,3.5 8,9 15,3.5" fill="none" stroke="var(--navy)" stroke-width="1.3"/></svg>
          marla@dovecoteprops.com
        </li>
        <li>87 Tarrow Quay, Boston MA 02114</li>
      </ul>
      <div class="rule"></div>
      <p class="slogan">Timeless Homes, Refined Service</p>
    </div>
  </section>

  <section class="card card--back">
    <span class="brand__name">DOVECOTE REALTY</span>
  </section>

</main>
</body>
</html>
```